The Brandwell Firm

We need a new design for our letterhead and envelopes. We are a personal injury and criminal defense firm so we need something modern and clean, but more on the professional/traditional side. Our new logo has two colors and is attached to the file so we need something that works well with those colors/matches the design. The following information needs to be on the letterhead:
Phone: (555) 214-3370
Fax: (555) 214-5186
Toll-Free: (888) 431-2059
Post Office Box 4721
Millbrook, SC 29555-4721
HarmClaimCounsel.example
PalmettoTrialAdvocates.example

Target Market(s)

Clients, government agencies, other law firms

Industry/Entity Type

Legal

Font styles to use
Sans Serif
Other font styles liked:
• Arial

Colors

Designer to choose colors to be used in the design.

Requirements
Must have
• Must look professional and clean, modern
Nice to have
• I would like to see a design that works with the logo but does not distract from the content that will be printed on it
Should not have
• Too many colors or crazy designs.

```html
<!DOCTYPE html>
<html lang="en">
<head>
<meta charset="utf-8">
<title>The Brandwell Firm – Stationery</title>
<link href="https://fonts.googleapis.com/css2?family=Lato:wght@400;700&display=swap" rel="stylesheet">
<style>
  :root {
    --backdrop: #d8d8d8;
    --paper: #ededed;
    --brand-red: #c7202b;
    --brand-blue: #2d2d88;
    --ink: #555555;
    --ink-dark: #333333;
  }
  * { margin: 0; padding: 0; box-sizing: border-box; }
  html, body { width: 1200px; height: 810px; overflow: hidden; }
  body {
    background: var(--backdrop);
    font-family: "Lato", Arial, sans-serif;
    color: var(--ink);
    position: relative;
  }

  /* Shared stationery elements */
  .sheet { position: absolute; background: var(--paper); }
  .edge-band { position: absolute; left: 0; top: 0; bottom: 0; width: 15px; }
  .edge-band .band-red { position: absolute; left: 0; top: 0; width: 100%; background: var(--brand-red); }
  .edge-band .band-blue { position: absolute; left: 0; bottom: 0; width: 100%; background: var(--brand-blue); }

  .brand-lockup { position: absolute; display: flex; align-items: center; gap: 8px; }
  .brand-dot { width: 16px; height: 16px; border-radius: 50%; background: var(--brand-blue); flex: none; }
  .brand-name { color: var(--brand-red); font-weight: 700; font-size: 20px; line-height: 1.1; letter-spacing: 0.3px; }

  /* Letterhead */
  .letterhead { left: 138px; top: 111px; width: 435px; height: 613px; }
  .letterhead .band-red { height: 126px; }
  .letterhead .band-blue { height: 484px; }
  .letterhead .brand-lockup { left: 43px; top: 52px; }

  .contact-block { position: absolute; left: 312px; top: 53px; font-size: 7.2px; line-height: 9.2px; color: var(--ink-dark); }
  .contact-address { margin-bottom: 6px; }
  .contact-row { display: flex; }
  .contact-label { color: var(--brand-blue); font-weight: 700; width: 32px; }
  .contact-sep { width: 6px; }

  .recipient { position: absolute; left: 43px; top: 200px; font-size: 7.6px; line-height: 11.4px; }
  .letter-body { position: absolute; left: 43px; top: 268px; width: 362px; font-size: 7.6px; line-height: 11.3px; text-align: justify; }
  .letter-body p + p { margin-top: 11px; }
  .signature { position: absolute; left: 43px; top: 435px; width: 84px; height: 52px; background: linear-gradient(90deg, rgba(45,45,136,0.18), rgba(45,45,136,0.08)); border-radius: 4px; }
  .signatory { position: absolute; left: 43px; top: 500px; font-size: 7.4px; }
  .letter-footer { position: absolute; left: 45px; top: 584px; font-size: 7.6px; color: var(--ink-dark); }
  .letter-footer .divider { color: var(--brand-blue); font-weight: 700; margin: 0 5px; }

  /* Envelope back */
  .envelope-back { left: 619px; top: 194px; width: 444px; height: 221px; }
  .envelope-flap { position: absolute; left: 0; top: 0; width: 444px; height: 66px; }
  .flap-name { position: absolute; left: 0; right: 0; top: 22px; text-align: center; color: #ffffff; font-weight: 700; font-size: 11px; letter-spacing: 0.3px; }

  /* Envelope front */
  .envelope-front { left: 618px; top: 444px; width: 445px; height: 221px; }
  .envelope-front .edge-band { width: 14px; }
  .envelope-front .band-red { height: 102px; }
  .envelope-front .band-blue { height: 117px; }
  .envelope-front .brand-lockup { left: 29px; top: 54px; }
  .return-address { position: absolute; left: 29px; top: 188px; font-size: 7.2px; line-height: 9.2px; color: var(--ink-dark); }
</style>
</head>
<body>

  <section class="sheet letterhead" aria-label="Letterhead">
    <div class="edge-band"><div class="band-red"></div><div class="band-blue"></div></div>

    <div class="brand-lockup">
      <span class="brand-dot"></span>
      <span class="brand-name">The Brandwell Firm</span>
    </div>

    <div class="contact-block">
      <div class="contact-address">Post Office Box 4721<br>Millbrook, SC 29555-4721</div>
      <div class="contact-row"><span class="contact-label">Phone</span><span class="contact-sep">:</span><span>(555) 214-3370</span></div>
      <div class="contact-row"><span class="contact-label">Fax</span><span class="contact-sep">:</span><span>(555) 214-5186</span></div>
      <div class="contact-row"><span class="contact-label">Toll-Free</span><span class="contact-sep">:</span><span>(888) 431-2059</span></div>
    </div>

    <div class="recipient">
      Dear Hollister<br>
      Kestrel Print Works Corporation<br>
      Department Design
    </div>

    <div class="letter-body">
      <p>Lorem ipsum dolor sit amet, consectetuer adipiscing elit. Aenean commodo ligula eget dolor. Aenean massa. Cum sociis natoque penatibus et magnis dis parturient montes, nascetur ridiculus mus. Donec quam felis, ultricies nec, pellentesque eu, pretium quis, sem. Nulla consequat massa quis enim. Donec pede justo, fringilla vel, aliquet nec, vulputate eget, arcu. In enim justo, rhoncus ut, imperdiet a, venenatis vitae, justo. Nullam dictum felis eu pede mollis pretium. Integer tincidunt. Cras dapibus. Vivamus elementum semper nisi.Nullam dictum felis eu pede mollis pretium. Integer tincidunt. Cras dapibus. Vivamus elementum semper nisi.felis eu pede mollis pretium. Integer tincidunt. Cras dapibus.</p>
      <p>Quisque rutrum. Aenean imperdiet. Etiam ultricies nisi vel augue. Curabitur ullamcorper ultricies nisi. Nam eget dui. Etiam rhoncus. Maecenas tempus, tellus eget condimentum rhoncus, sem quam semper libero, sit amet adipiscing sem neque sed ipsum.felis pede mollis pretium. I am tincidunt. Cras dapibus.</p>
    </div>

    <div class="signature" role="img" aria-label="Handwritten signature of the director"></div>
    <div class="signatory">Director/Excecutive Director</div>

    <div class="letter-footer">
      www.HarmClaimCounsel.example<span class="divider">|</span>www.PalmettoTrialAdvocates.example
    </div>
  </section>

  <section class="sheet envelope-back" aria-label="Envelope back">
    <svg class="envelope-flap" viewBox="0 0 444 66" aria-hidden="true">
      <path d="M0 0 H444 L436 54 Q434 64 424 64 H20 Q10 64 8 54 Z" fill="var(--brand-blue)"/>
    </svg>
    <div class="flap-name">The Brandwell Firm</div>
  </section>

  <section class="sheet envelope-front" aria-label="Envelope front">
    <div class="edge-band"><div class="band-red"></div><div class="band-blue"></div></div>

    <div class="brand-lockup">
      <span class="brand-dot"></span>
      <span class="brand-name">The Brandwell Firm</span>
    </div>

    <div class="return-address">Post Office Box 4721<br>Millbrook, SC 29555-4721</div>
  </section>

</body>
</html>
```